Business Card for my New Brokerage

Looking to get a business card design for my new Real Estate Brokerage.
I want it with Picture, Phone Number, Email, Website, Office Address
Name and Designation. Please add logo too.

Target Market(s)

Real Estate Investors or Home Buyers

Industry/Entity Type

Real Estate

Contact Information for Business Card

Name, Email, Phone Number, website, email, office address

Colors
EB3D1F
EC4F4E
F09395
F8D3D4
FCEDEE

Requirements
Must have
• Minimalistic, Clean, Modern, Photo
Nice to have
• White and Red Colors

```html
<!DOCTYPE html>
<html lang="en">
<head>
<meta charset="UTF-8">
<title>Beacon Realty Co – Business Card</title>
<link href="https://fonts.googleapis.com/css2?family=Montserrat:wght@500;800&family=Arimo:wght@400&display=swap" rel="stylesheet">
<style>
  :root {
    --brand-red: #d90000;
    --brand-red-dark: #c40000;
    --paper: #ffffff;
    --ink: #3a3a3a;
    --stage: #e9e9e9;
    --photo-light: #ececea;
    --photo-dark: #2b2b2b;
  }
  * { margin: 0; padding: 0; box-sizing: border-box; }
  html, body { width: 1200px; height: 1015px; overflow: hidden; }
  body { background: var(--stage); position: relative; font-family: "Arimo", Arial, sans-serif; }

  .card {
    position: absolute;
    left: 280px;
    width: 640px;
    height: 366px;
    overflow: hidden;
    box-shadow: 0 6px 18px rgba(0,0,0,.18);
  }

  /* Front */
  .card--front { top: 90px; background: var(--brand-red); }
  .card--front .wordmark {
    position: absolute; left: 0; right: 0; top: 122px;
    text-align: center; color: var(--paper);
  }
  .wordmark__name {
    font-family: "Montserrat", sans-serif; font-weight: 800;
    font-size: 76px; line-height: 1; letter-spacing: 1px;
  }
  .wordmark__sub {
    font-family: "Montserrat", sans-serif; font-weight: 800;
    font-size: 22px; letter-spacing: 12px; margin-top: 8px; padding-left: 12px;
  }

  /* Back */
  .card--back { top: 536px; background: var(--paper); }
  .card__band { position: absolute; left: 0; top: 0; bottom: 0; width: 12px; background: var(--brand-red); }

  .card--back .wordmark {
    position: absolute; left: 52px; top: 40px; color: var(--brand-red);
  }
  .card--back .wordmark__name { font-size: 56px; }
  .card--back .wordmark__sub { font-size: 16px; letter-spacing: 9px; margin-top: 6px; padding-left: 0; }

  .portrait {
    position: absolute; left: 132px; top: 158px; width: 252px; height: 208px;
    background: linear-gradient(160deg, var(--photo-light) 0%, #d8d8d6 55%, var(--photo-dark) 100%);
  }

  .profile { position: absolute; left: 410px; top: 48px; right: 28px; color: var(--ink); }
  .profile__rule-top { height: 1.5px; background: var(--brand-red); margin-bottom: 14px; }
  .profile__name {
    font-family: "Montserrat", sans-serif; font-weight: 800;
    font-size: 26px; color: var(--brand-red); line-height: 1.05;
  }
  .profile__title { font-size: 15px; margin-top: 4px; }
  .profile__rule { height: 1.5px; background: var(--brand-red); width: 150px; margin: 10px 0 12px; }

  .contact-list { list-style: none; }
  .contact-list li { display: flex; align-items: center; gap: 8px; font-size: 14px; line-height: 1.55; }
  .contact-list svg { width: 14px; height: 14px; fill: var(--brand-red); flex: none; }

  .address { font-size: 14px; line-height: 1.45; margin-top: 16px; padding-left: 22px; }
</style>
</head>
<body>

  <section class="card card--front" aria-label="Card front">
    <div class="wordmark">
      <div class="wordmark__name">BEACON</div>
      <div class="wordmark__sub">REALTY CO</div>
    </div>
  </section>

  <section class="card card--back" aria-label="Card back">
    <div class="card__band"></div>

    <div class="wordmark">
      <div class="wordmark__name">BEACON</div>
      <div class="wordmark__sub">REALTY CO</div>
    </div>

    <div class="portrait" role="img" aria-label="Portrait photo of the managing director in a dark suit"></div>

    <div class="profile">
      <div class="profile__rule-top"></div>
      <h1 class="profile__name">MARCUS HALE</h1>
      <p class="profile__title">Managing Director</p>
      <div class="profile__rule"></div>

      <ul class="contact-list">
        <li>
          <svg viewBox="0 0 24 24" aria-hidden="true"><path d="M6.6 10.8a15.1 15.1 0 0 0 6.6 6.6l2.2-2.2a1 1 0 0 1 1-.25 11.4 11.4 0 0 0 3.6.57 1 1 0 0 1 1 1V20a1 1 0 0 1-1 1A17 17 0 0 1 3 4a1 1 0 0 1 1-1h3.5a1 1 0 0 1 1 1c0 1.25.2 2.45.57 3.57a1 1 0 0 1-.25 1z"/></svg>
          044-555 010 234
        </li>
        <li>
          <svg viewBox="0 0 24 24" aria-hidden="true"><path d="M2 5h20v14H2z M2 5l10 8 10-8" fill="none" stroke="#d90000" stroke-width="2.4"/></svg>
          info@beaconrealty.com
        </li>
        <li>
          <svg viewBox="0 0 24 24" aria-hidden="true"><circle cx="12" cy="12" r="10" fill="none" stroke="#d90000" stroke-width="2"/><path d="M2 12h20M12 2c3 3 3 17 0 20M12 2c-3 3-3 17 0 20" fill="none" stroke="#d90000" stroke-width="1.6"/></svg>
          www.beaconrealty.com
        </li>
      </ul>

      <p class="address">421, Address line goes here<br>45452, Country Name</p>
    </div>
  </section>

</body>
</html>
```